Request for Business Card Design

Hi. My name is Marlene, I am looking for a new business card design for my company, Quarrow Signal Instruments, LLC. I really like the design you did for Tarsel Venture and was hoping you could do something similar using our full logo and our mark. I am also open to any raised texture design using our mark. I have attached our full logo, which would need to be somewhere on the card, as well as the mark in both outline and full form, as well as our brand colors / guide. The card does not have to be white, as long as our logo and mark appear. I actually like darker colored business cards more, but am open to all options. If you are interested in working with me, please let me know. We would also take the business card design into letterhead design if you can do that.

```html
<!DOCTYPE html>
<html lang="en">
<head>
<meta charset="utf-8">
<title>Quarrow Signal Instruments – Business Card</title>
<link rel="stylesheet" href="https://fonts.googleapis.com/css2?family=Roboto:wght@400;500;700&display=swap">
<style>
  :root {
    --backdrop: #ababab;
    --card-dark: #1f1f1f;
    --brand-blue: #0a9bc2;
    --name-blue: #0b9cc4;
    --text-light: #cfcfcf;
    --white: #ffffff;
  }
  * { box-sizing: border-box; margin: 0; padding: 0; }
  html, body {
    width: 1093px;
    height: 1200px;
    overflow: hidden;
    background: var(--backdrop);
    font-family: "Roboto", Arial, sans-serif;
  }
  .canvas { position: relative; width: 1093px; height: 1200px; }

  .card {
    position: absolute;
    left: 265px;
    width: 578px;
    height: 356px;
    border-radius: 28px;
    overflow: hidden;
  }
  .card--front { top: 226px; background: var(--card-dark); }
  .card--back  { top: 621px; background: var(--brand-blue); }

  /* Person */
  .person { position: absolute; left: 26px; top: 48px; }
  .person__name {
    font-weight: 700;
    font-size: 24px;
    line-height: 1;
    color: var(--name-blue);
    letter-spacing: 0.2px;
  }
  .person__title {
    margin-top: 1px;
    font-weight: 400;
    font-size: 17px;
    color: var(--text-light);
  }

  /* Brand lockup */
  .brand { position: absolute; display: flex; align-items: center; }
  .brand__dot { border-radius: 50%; flex: none; }
  .brand__words { font-weight: 500; line-height: 1; text-transform: uppercase; }
  .brand__main { display: block; }
  .brand__sub { display: block; }

  .brand--front { right: 30px; top: 52px; gap: 14px; }
  .brand--front .brand__dot { width: 40px; height: 40px; background: var(--brand-blue); }
  .brand--front .brand__words { color: var(--white); }
  .brand--front .brand__main { font-size: 28px; letter-spacing: 3.4px; }
  .brand--front .brand__sub { font-size: 10.5px; letter-spacing: 0.4px; margin-top: 5px; }

  .brand--back { left: 110px; top: 136px; gap: 34px; }
  .brand--back .brand__dot { width: 74px; height: 74px; background: var(--white); }
  .brand--back .brand__words { color: var(--white); }
  .brand--back .brand__main { font-size: 44px; letter-spacing: 5.2px; }
  .brand--back .brand__sub { font-size: 15.6px; letter-spacing: 0.7px; margin-top: 8px; }

  /* Contacts */
  .contacts {
    position: absolute;
    left: 26px;
    top: 256px;
    list-style: none;
    font-size: 17.5px;
    color: var(--text-light);
  }
  .contacts li { display: flex; align-items: center; height: 21px; }
  .contacts svg { width: 16px; height: 16px; margin-right: 7px; flex: none; }

  .address {
    position: absolute;
    right: 30px;
    top: 277px;
    text-align: right;
    font-style: normal;
    font-size: 17.5px;
    line-height: 21px;
    color: var(--text-light);
  }
</style>
</head>
<body>
<main class="canvas">

  <section class="card card--front" aria-label="Card front">
    <div class="person">
      <h1 class="person__name">DORIAN VALE</h1>
      <p class="person__title">Managing Director</p>
    </div>

    <div class="brand brand--front">
      <span class="brand__dot" aria-hidden="true"></span>
      <p class="brand__words">
        <span class="brand__main">Quarrow</span>
        <span class="brand__sub">Signal Instruments</span>
      </p>
    </div>

    <ul class="contacts">
      <li>
        <svg viewBox="0 0 16 16" aria-hidden="true"><path fill="#0a9bc2" d="M3.6 1.5l2.3 2.4-1.3 1.6c.9 2 2.6 3.7 4.5 4.6l1.6-1.3 2.4 2.3-1.6 2.2C6.5 13 2.8 9.4 1.6 3.1z"/><path fill="none" stroke="#0a9bc2" stroke-width="1.3" d="M9.5 2.2a4.5 4.5 0 0 1 4.2 4.2M9.3 4.6a2.2 2.2 0 0 1 2 2"/></svg>
        044-318 602 547
      </li>
      <li>
        <svg viewBox="0 0 16 16" aria-hidden="true"><rect x="0.5" y="3" width="15" height="10.5" fill="#0a9bc2"/><path fill="none" stroke="#1f1f1f" stroke-width="1.2" d="M0.8 3.4L8 9.2l7.2-5.8M0.8 13.2l5-4.4M15.2 13.2l-5-4.4"/></svg>
        hello@quarrowsignal.com
      </li>
      <li>
        <svg viewBox="0 0 16 16" aria-hidden="true"><g fill="none" stroke="#0a9bc2" stroke-width="1.3"><circle cx="8" cy="8" r="6.8"/><ellipse cx="8" cy="8" rx="3" ry="6.8"/><path d="M1.2 8h13.6M2.3 4.6h11.4M2.3 11.4h11.4"/></g></svg>
        www.quarrowsignal.com
      </li>
    </ul>

    <address class="address">
      87, Harbor Lane, Suite 4<br>
      30917,Norland
    </address>
  </section>

  <section class="card card--back" aria-label="Card back">
    <div class="brand brand--back">
      <span class="brand__dot" aria-hidden="true"></span>
      <p class="brand__words">
        <span class="brand__main">Quarrow</span>
        <span class="brand__sub">Signal Instruments</span>
      </p>
    </div>
  </section>

</main>
</body>
</html>
```